AUTOMOTIVE/ CAR REPAIRS / CRASH REPAIRS / PAINT SPRAYING AND PANEL BEATING

AUTOMOTIVE REPAIR. CAR / MOTORCYCLES GOT LOGO DESIGN / DID THINK ABOUT LINKOVA DONT NOALREADY HAVE WEB ADRESS www.brenvashine.co.uk and mail sales@brenvashine,co.uk NEED SOMETHINK I CAN MANAGE TO UPLOAD PICTURES IN TO A GALLERY OR SOMETHINGLIKE THAT I ALSO SELL CAR AND MOTORCYCLES MAYBE A SELLS PAGE WITH A TILLWAVE LINK

Target Market(s)

TRADE / GENERAL PUBLIC

Industry/Entity Type

Automotive

Coding

Coded - Design and coding required

Number of Pages Required

4 page

Font styles to use
Serif
Sans Serif

Colors

Designer to choose colors to be used in the design.

Requirements
Must have
• GALLERY/ SHOP TO SALE CARS AND MOTORCYCLE / LOGOS OF MATERIALS I USE DORFLINT / KEBO / VASTINCO / Q WRAP / GLENBRUSH
• CONTACT US
Nice to have
• TILLWAVE / EASY TO MANAGE / VIDEO CLIP OF DORFLINT HUE PLANNER Z7
• SWIFT BLEND PAINT TONVIEW WETLINE AND TULVOKE

```html
<!DOCTYPE html>
<html lang="en">
<head>
<meta charset="utf-8">
<title>Brenvashine Bodyshop</title>
<link href="https://fonts.googleapis.com/css2?family=Lato:wght@300;400;700;900&display=swap" rel="stylesheet">
<style>
:root{
  --red:#d9141c;
  --ink:#111;
  --text:#333;
  --muted:#555;
  --grey:#efeeec;
  --line:#ddd;
  --black:#000;
  --white:#fff;
}
*{box-sizing:border-box;margin:0;padding:0}
html,body{width:1200px;height:5286px;overflow:hidden;background:var(--white)}
body{font-family:'Lato',Arial,sans-serif;color:var(--text);position:relative}
.section{position:absolute;left:0;width:1200px}
.btn{display:inline-block;background:var(--red);color:var(--white);font-weight:700;font-size:17px;padding:14px 30px;text-decoration:none}
.heading{font-weight:400;color:var(--ink);text-transform:uppercase;font-size:38px;text-align:center;letter-spacing:.5px}

/* hero */
.hero{top:0;height:640px;background:linear-gradient(180deg,#1d2026 0%,#3a3f47 35%,#1a1b1f 70%,#0d0d0f 100%)}
.hero-photo{position:absolute;left:0;top:0;width:1200px;height:600px;background:radial-gradient(ellipse at 52% 62%,#b3141a 0%,#6a0e12 22%,rgba(40,40,45,0) 48%),linear-gradient(180deg,#4a5059 0%,#2a2d33 50%,#a68a3a 72%,#15151a 100%)}
.brand{position:absolute;left:76px;top:26px;color:var(--white);font-weight:700;font-size:30px;letter-spacing:5px;line-height:1.1}
.nav{position:absolute;right:70px;top:48px;display:flex;gap:28px}
.nav a{color:var(--white);text-decoration:none;font-size:15px;text-transform:uppercase}
.nav a.active{border-bottom:2px solid var(--red);padding-bottom:4px}
.hero-arrow{position:absolute;top:286px}
.hero-title{position:absolute;top:410px;width:1200px;text-align:center;color:var(--white)}
.hero-title h1{font-weight:400;font-size:46px;text-transform:uppercase;line-height:1.15}
.hero-title p{font-size:44px;line-height:1.2}
.hero .btn{position:absolute;left:523px;top:534px;font-size:17px;padding:13px 26px}
.hero-curve{position:absolute;left:0;top:540px}

/* about */
.about{top:640px;height:776px;text-align:center}
.about .heading{margin-top:64px}
.about .sub{font-weight:700;font-size:16px;color:var(--ink);margin-top:22px}
.about .lead{font-size:22px;color:var(--ink);width:960px;margin:22px auto 0;line-height:1.3}
.about .body{font-size:13.5px;color:var(--muted);width:860px;margin:26px auto 0;line-height:1.7}
.about .cars{width:800px;height:240px;margin:30px auto 0;background:linear-gradient(90deg,#e58a14 0%,#2b2b2b 25%,#d71a20 50%,#6ac43a 80%,#4c9a2a 100%);border-radius:120px 120px 40px 40px;opacity:.9}
.about .btn{margin-top:42px}

/* testimonial */
.testimonial{top:1416px;height:334px;background:var(--grey);text-align:center}
.quote-mark{margin-top:28px}
.testimonial blockquote{width:860px;margin:20px auto 0;font-size:19px;line-height:1.45;color:var(--ink)}
.testimonial cite{display:block;font-style:normal;font-size:28px;color:var(--ink);margin-top:26px}
.t-arrow{position:absolute;top:157px}

/* what we do */
.what{top:1750px;height:932px}
.what .heading{margin-top:52px}
.what .intro{text-align:center;font-weight:700;font-size:15px;width:760px;margin:22px auto 0;line-height:1.5;color:var(--ink)}
.why{position:absolute;left:78px;top:245px;width:510px;z-index:2}
.why h2{font-weight:400;font-size:38px;color:var(--ink)}
.why p{font-size:12.5px;line-height:1.75;color:var(--muted);margin-top:22px}
.ticks{list-style:none;margin-top:28px}
.ticks li{position:relative;padding-left:30px;margin-bottom:20px}
.ticks li svg{position:absolute;left:0;top:3px}
.ticks strong{display:block;font-weight:400;font-size:17px;color:var(--ink)}
.ticks span{display:block;font-size:12.5px;color:var(--muted);line-height:1.7;margin-top:4px}
.bike{position:absolute;left:690px;top:225px;width:415px;height:275px;background:radial-gradient(ellipse at 50% 55%,#3a3a3a 0%,#8a8a8a 45%,#f2f2f2 75%)}
.classics{position:absolute;left:612px;top:530px;width:532px;height:270px;background:linear-gradient(100deg,#7b8aa0 0%,#d01a20 30%,#e21c22 55%,#8fa3b8 85%);border-radius:135px 135px 60px 60px}

/* services */
.services{top:2682px;height:657px;background:var(--grey);text-align:center}
.services .heading{margin-top:56px}
.cards{display:flex;gap:37px;justify-content:center;margin-top:52px}
.card{width:306px;height:314px;background:var(--white);border:1px solid var(--line);padding:40px 26px 0}
.card .icon{width:80px;height:80px;margin:0 auto;border:3px solid var(--red);border-radius:8px}
.card h3{font-weight:400;font-size:27px;color:var(--ink);margin-top:22px;line-height:1.25}
.card p{font-size:11.5px;color:var(--muted);margin-top:18px;line-height:1.8}
.services .btn{margin-top:56px}

/* gallery */
.gallery{top:3339px;height:857px;text-align:center}
.gallery .heading{margin-top:50px}
.grid{display:grid;grid-template-columns:350px 350px 353px;grid-template-rows:255px 255px;gap:1px;width:1055px;margin:38px auto 0}
.grid div{width:100%;height:100%}
.g1{background:linear-gradient(135deg,#d8c23a,#4e7a24 55%,#2c3a1a)}
.g2{background:linear-gradient(180deg,#3a3a3a,#0d0d0d)}
.g3{background:linear-gradient(160deg,#c6d6e6,#5a5a5a 55%,#2a2a2a)}
.g4{background:linear-gradient(180deg,#1c1c1c,#444 60%,#111)}
.g5{background:linear-gradient(180deg,#6a6a6a,#e8e8e8 55%,#7a7a7a)}
.g6{background:linear-gradient(160deg,#dcdcdc,#9aa2a8 55%,#6a6e72)}
.gallery .btn{margin-top:22px}
.brands{display:flex;justify-content:space-between;align-items:center;width:1000px;margin:40px auto 0}
.brands span{font-weight:900;font-size:28px;color:#2a2a2a;letter-spacing:.5px}

/* contact */
.contact{top:4196px;height:493px;background:var(--grey)}
.info{position:absolute;left:72px;top:62px;width:260px}
.info-item{position:relative;padding-left:52px;margin-bottom:30px}
.info-item svg{position:absolute;left:0;top:2px}
.info-item h4{font-weight:400;font-size:19px;color:var(--ink)}
.info-item p{font-size:13px;color:var(--muted);line-height:2;margin-top:8px}
.info-item p.phone{font-size:21px;color:var(--ink);margin-top:6px}
.estimate{position:absolute;left:410px;top:72px;width:705px}
.estimate h3{font-weight:400;font-size:26px;color:var(--ink);text-transform:uppercase}
.estimate .addr{font-size:13px;color:var(--muted);margin-top:16px}
.fields{display:grid;grid-template-columns:350px 345px;gap:10px;margin-top:46px}
.field{background:var(--white);height:38px;font-size:13px;color:var(--muted);padding:11px 16px}
.field.wide{grid-column:1 / span 2;height:52px;padding-top:14px}
.estimate .note{font-size:13px;color:var(--muted);margin-top:38px}
.estimate .btn{margin-top:26px;font-size:16px;padding:13px 22px}

/* footer */
.footer{top:4894px;height:392px;background:var(--black);text-align:center;color:var(--white)}
.map{position:absolute;left:86px;top:4689px;width:1020px;height:297px;background:linear-gradient(120deg,#eef0ee 0%,#e6ebe5 60%,#c9e3c4 75%,#e9ece8 100%);border:1px solid #ccc}
.footer-brand{position:absolute;top:155px;width:1200px;font-weight:700;font-size:30px;letter-spacing:5px;line-height:1.1}
.footer-nav{position:absolute;top:247px;width:1200px;display:flex;justify-content:center;gap:26px}
.footer-nav a{color:var(--white);text-decoration:none;font-size:15px;text-transform:uppercase}
.social{position:absolute;top:285px;width:1200px;display:flex;justify-content:center;gap:22px;font-size:12px}
.copy{position:absolute;top:330px;width:1200px;font-size:13px}
</style>
</head>
<body>

<header class="section hero">
  <div class="hero-photo" role="img" aria-label="Red sports car cornering on a mountain road under a stormy sky"></div>
  <div class="brand">BRENVASHINE<br><span style="font-size:14px;letter-spacing:9px;font-weight:700">BODYSHOP</span></div>
  <nav class="nav">
    <a class="active" href="#">Home</a><a href="#">About Us</a><a href="#">Service</a><a href="#">Custom</a><a href="#">Gallery</a><a href="#">Contact</a>
  </nav>
  <svg class="hero-arrow" style="left:106px" width="14" height="22" viewBox="0 0 14 22"><path d="M12 2 3 11l9 9" fill="none" stroke="#fff" stroke-width="3"/></svg>
  <svg class="hero-arrow" style="left:1080px" width="14" height="22" viewBox="0 0 14 22"><path d="M2 2l9 9-9 9" fill="none" stroke="#fff" stroke-width="3"/></svg>
  <div class="hero-title">
    <h1>Your One Stop Body Shop</h1>
    <p>The home of paint perfection</p>
  </div>
  <a class="btn" href="#">SHOP NOW</a>
  <svg class="hero-curve" width="1200" height="100" viewBox="0 0 1200 100" preserveAspectRatio="none">
    <path d="M0 30 Q600 90 1200 30 L1200 100 L0 100Z" fill="#fff"/>
    <path d="M0 30 Q600 90 1200 30" fill="none" stroke="#d9141c" stroke-width="8"/>
  </svg>
</header>

<section class="section about">
  <h2 class="heading">Brenvashine Your One Stop Bodyshop</h2>
  <p class="sub">Fully qualified trained technicians family run business established over 30 years</p>
  <p class="lead">Brenvashine, based in Corrowby, Halvenshire established in August, 1985 has grown to become Halvenshire's premiere manufacturer approved accident repair centre.</p>
  <p class="body">Equipped with the latest technology and factory trained technicians, we process accident repairs for all leading insurance and vehicle management companies, specialising in accident repairs for most prestige vehicles manufacturers. We are proud to maintain a close working partnership with several local dealership networks.</p>
  <p class="body" style="margin-top:18px">Brenvashine aims to continually set new standards of quality control and customer care, by ensuring an accident repair service which exceeds all expectations whilst providing a fully guaranteed, quality repair to meet the customers needs.</p>
  <div class="cars" role="img" aria-label="Row of cars: orange hatchback, black muscle car, red classic sports car, engine and green hatchback"></div>
  <a class="btn" href="#">Read More</a>
</section>

<section class="section testimonial">
  <svg class="quote-mark" width="76" height="76" viewBox="0 0 76 76"><circle cx="38" cy="38" r="38" fill="#d9141c"/><text x="38" y="66" text-anchor="middle" font-family="Lato,sans-serif" font-weight="900" font-size="72" fill="#fff">&#8220;</text></svg>
  <svg class="t-arrow" style="left:106px" width="12" height="20" viewBox="0 0 12 20"><path d="M10 2 3 10l7 8" fill="none" stroke="#111" stroke-width="3"/></svg>
  <svg class="t-arrow" style="left:1080px" width="12" height="20" viewBox="0 0 12 20"><path d="M2 2l7 8-7 8" fill="none" stroke="#111" stroke-width="3"/></svg>
  <blockquote>" Your company did a great job on my Velmont Roadster. I was very pleased with the service you provided and the extra attention to detail.&nbsp; I would recommend Brenvashine to anyone needing any sort of car body repairs "</blockquote>
  <cite>Mr R Alcombe</cite>
</section>

<section class="section what">
  <h2 class="heading">What We Do</h2>
  <p class="intro">From the repair of the smallest dents and scratches to major auto repair work, Brenvashine is set up to meet your needs.</p>
  <div class="bike" role="img" aria-label="Black chrome cruiser motorcycle"></div>
  <div class="classics" role="img" aria-label="Line of classic sports cars, red and silver-blue, one under primer"></div>
  <div class="why">
    <h2>WHY US</h2>
    <p>As a small company we are able to offer an exceptionally personal service. Whenever you call us we aim for you to be able to speak directly to the person performing your car body repairs, who will give you plain speaking, objective advice. This, combined with our many years' experience and competitive prices makes us the perfect choice for those in need of any car body repair. (Please call or email us from our contact page to arrange a estimate appointment)</p>
    <ul class="ticks">
      <li><svg width="18" height="14" viewBox="0 0 18 14"><path d="M2 7l5 5L16 2" fill="none" stroke="#d9141c" stroke-width="3"/></svg><strong>Full or part resprays</strong><span>Single panel resprays to full<br>car resprays</span></li>
      <li><svg width="18" height="14" viewBox="0 0 18 14"><path d="M2 7l5 5L16 2" fill="none" stroke="#d9141c" stroke-width="3"/></svg><strong>Dent &amp; scratch removal</strong><span>From small paintless dent repairs to full panel<br>replacements. Scratches, chips &amp; paint repairs undertaken</span></li>
      <li><svg width="18" height="14" viewBox="0 0 18 14"><path d="M2 7l5 5L16 2" fill="none" stroke="#d9141c" stroke-width="3"/></svg><strong>Bumper repair</strong><span>Bumper scuffs, plastic bumper repairs and full bumper replacements. Full factory<br>matched colours.</span></li>
      <li><svg width="18" height="14" viewBox="0 0 18 14"><path d="M2 7l5 5L16 2" fill="none" stroke="#d9141c" stroke-width="3"/></svg><strong>Accident repair</strong><span>All accident repair undertaken. Just one call to Brenvashine and we'll help you<br>take the first steps towards getting your vehicle repaired and back on the road.</span></li>
      <li><svg width="18" height="14" viewBox="0 0 18 14"><path d="M2 7l5 5L16 2" fill="none" stroke="#d9141c" stroke-width="3"/></svg><strong>Alloy wheel's refurbished, repaired &amp; PAinted</strong></li>
    </ul>
  </div>
</section>

<section class="section services">
  <h2 class="heading">Our Service</h2>
  <div class="cards">
    <div class="card"><div class="icon" role="img" aria-label="Car on a lift icon"></div><h3>Full or part<br>resprays</h3><p>Sometimes a vehicle would simply benefit from having a complete new coat of paint.</p></div>
    <div class="card"><div class="icon" role="img" aria-label="Robotic arm over a car icon"></div><h3>Dents &amp; scratch<br>removal</h3><p>(SMART repair, SMART is an abbreviation of Small to Medium Area Repair Techniques )</p></div>
    <div class="card"><div class="icon" role="img" aria-label="Damaged car bumper icon"></div><h3>Bumper<br>repair</h3><p>Car bumper scuff damage can not only harm the appearance of your vehicle.</p></div>
  </div>
  <a class="btn" href="#">View More Services</a>
</section>

<section class="section gallery">
  <h2 class="heading">Our Gallery</h2>
  <div class="grid">
    <div class="g1" role="img" aria-label="Sport motorcycle on a sunlit forest road"></div>
    <div class="g2" role="img" aria-label="Black saloon front view"></div>
    <div class="g3" role="img" aria-label="Chrome cruiser motorcycle on a hill"></div>
    <div class="g4" role="img" aria-label="Black car rear view in the workshop"></div>
    <div class="g5" role="img" aria-label="White coupe front view in the workshop"></div>
    <div class="g6" role="img" aria-label="Silver car outside the bodyshop unit"></div>
  </div>
  <a class="btn" href="#">View More</a>
  <div class="brands">
    <span>DORFLINT</span><span>KEBO</span><span>VASTINCO</span><span>Q WRAP</span><span>GLENBRUSH</span>
  </div>
</section>

<section class="section contact">
  <div class="info">
    <div class="info-item">
      <svg width="30" height="40" viewBox="0 0 30 40"><path d="M15 0C7 0 0 6 0 14c0 10 15 26 15 26s15-16 15-26C30 6 23 0 15 0z" fill="#222"/><circle cx="15" cy="14" r="5" fill="#efeeec"/></svg>
      <h4>Address</h4>
      <p>Kestrel Business Park,<br>Ferrow Lane, Corrowby,<br>Halvenshire,<br>HV12 7QN</p>
    </div>
    <div class="info-item">
      <svg width="34" height="34" viewBox="0 0 24 24"><path d="M6.6 10.8a15.1 15.1 0 0 0 6.6 6.6l2.2-2.2c.3-.3.7-.4 1-.2 1.1.4 2.3.6 3.6.6.6 0 1 .4 1 1V20c0 .6-.4 1-1 1A17 17 0 0 1 3 4c0-.6.4-1 1-1h3.5c.6 0 1 .4 1 1 0 1.3.2 2.5.6 3.6.1.3 0 .7-.2 1z" fill="#222"/></svg>
      <h4>Call Us</h4>
      <p class="phone">07700 914 362</p>
    </div>
    <div class="info-item">
      <svg width="36" height="28" viewBox="0 0 36 28"><rect width="36" height="28" rx="3" fill="#222"/><path d="M2 3l16 13L34 3" fill="none" stroke="#efeeec" stroke-width="2.5"/></svg>
      <h4>Support</h4>
      <p>www.brenvashine.co.uk<br>sales@brenvashine,co.uk</p>
    </div>
  </div>
  <div class="estimate">
    <h3>Free Estimate Appointment</h3>
    <p class="addr">Brenvashine Bodyshop, Kestrel Business park Ferrow lane , Corrowby , Halvenshire, HV12 7QN</p>
    <div class="fields">
      <div class="field">Date</div><div class="field">Time</div>
      <div class="field wide">Price</div>
    </div>
    <p class="note">If you are unable to keep your appointment please contact us as soon as possible.</p>
    <a class="btn" href="#">Book an Appointment</a>
  </div>
</section>

<footer class="section footer">
  <div class="footer-brand">BRENVASHINE<br><span style="font-size:14px;letter-spacing:9px">BODYSHOP</span></div>
  <nav class="footer-nav"><a href="#">Home</a><a href="#">About Us</a><a href="#">Service</a><a href="#">Custom</a><a href="#">Gallery</a><a href="#">Contact</a></nav>
  <div class="social"><span>Linkova</span><span>Chirpa</span><span>Plusly</span><span>TILLWAVE</span></div>
  <p class="copy">&copy; 2019 &nbsp;|&nbsp; www.brenvashine.co.uk</p>
</footer>

<div class="map" role="img" aria-label="Street map of the bodyshop location with a red pin and a park to the east"></div>

</body>
</html>
```